New Year's card HTML

can you produce a best new years wishes 2018 design in HTML for our website as what I would like to send by email towards my network of candidates / customers ...

It must be wow, inspiring , design, meaningfull... MMM those people care about me, or those people will help me to go the extra mile, to help me to achieve my career goals, Your best move, enhance my possibilities, bring the love back

Target Market(s)

CEo's / CMO's/ HRDirectors network of 450k

Coding

Coded - Design and coding required

Number of Pages Required

1 page

Colors

Designer to choose colors to be used in the design.

Requirements
Must have
• Logo / visual / website adress www.moravintel.com and a call to action
Should not have
• no sound as our business is confidential

```html
<!DOCTYPE html>
<html lang="en">
<head>
<meta charset="utf-8">
<title>Moravintel – Happy New Year 2018</title>
<link rel="stylesheet" href="https://fonts.googleapis.com/css2?family=Cormorant+Garamond:wght@500&family=Pacifico&family=Roboto:wght@400;500&display=swap">
<style>
  :root {
    --night: #0b0c14;
    --deep-violet: #2a1a5e;
    --electric-blue: #2f5fd0;
    --neon-purple: #7a3cc8;
    --spectrum-gold: #c9a233;
    --white: #ffffff;
    --cta-copper: #b8641f;
    --arrow-green: #6fd23a;
    --figure-grey: #e6e6e6;
  }
  html, body {
    margin: 0;
    padding: 0;
    width: 1200px;
    height: 780px;
    overflow: hidden;
    background: var(--night);
  }
  .greeting-card {
    position: relative;
    width: 1200px;
    height: 780px;
    overflow: hidden;
    background: var(--night);
    color: var(--white);
  }
  .backdrop-visual {
    position: absolute;
    inset: 0;
    background:
      radial-gradient(ellipse 420px 300px at 900px 140px, rgba(201,162,51,0.55), transparent 70%),
      radial-gradient(ellipse 520px 360px at 820px 330px, rgba(47,95,208,0.55), transparent 70%),
      radial-gradient(ellipse 640px 420px at 700px 620px, rgba(122,60,200,0.6), transparent 70%),
      radial-gradient(ellipse 500px 300px at 250px 200px, rgba(42,26,94,0.5), transparent 70%),
      linear-gradient(160deg, #0d0f18 0%, #141633 45%, #1c1245 100%);
  }
  .mascot-visual {
    position: absolute;
    left: 680px;
    top: 510px;
    width: 520px;
    height: 270px;
    background:
      radial-gradient(ellipse 110px 150px at 430px 150px, rgba(230,230,230,0.9), transparent 75%),
      radial-gradient(ellipse 220px 70px at 190px 120px, rgba(111,210,58,0.75), transparent 75%);
  }
  .brand {
    position: absolute;
    top: 44px;
    left: 0;
    width: 100%;
    display: flex;
    justify-content: center;
    align-items: center;
    gap: 18px;
  }
  .brand-dot {
    width: 26px;
    height: 26px;
    border-radius: 50%;
    background: var(--white);
  }
  .brand-name {
    font-family: "Cormorant Garamond", serif;
    font-weight: 500;
    font-size: 42px;
    letter-spacing: 3px;
    color: var(--white);
    text-transform: uppercase;
    line-height: 1;
  }
  .headline {
    position: absolute;
    left: 0;
    top: 188px;
    width: 100%;
    margin: 0;
    text-align: center;
    font-family: "Pacifico", cursive;
    font-weight: 400;
    color: var(--white);
  }
  .headline-year {
    display: block;
    font-size: 150px;
    line-height: 190px;
    letter-spacing: 4px;
  }
  .headline-wish {
    display: block;
    font-size: 88px;
    line-height: 120px;
    margin-top: -38px;
  }
  .cta-button {
    position: absolute;
    left: 465px;
    top: 542px;
    width: 272px;
    height: 64px;
    border-radius: 32px;
    background: var(--cta-copper);
    color: var(--white);
    font-family: "Roboto", sans-serif;
    font-weight: 500;
    font-size: 21px;
    text-transform: uppercase;
    text-decoration: none;
    display: flex;
    align-items: center;
    justify-content: center;
  }
  .site-address {
    position: absolute;
    left: 32px;
    bottom: 26px;
    font-family: "Roboto", sans-serif;
    font-weight: 400;
    font-size: 18px;
    color: var(--white);
    text-decoration: none;
    line-height: 1;
  }
</style>
</head>
<body>
  <main class="greeting-card">
    <div class="backdrop-visual" role="img" aria-label="Abstract background of glowing light trails and a colourful grid of spectrum tiles on a dark night tone"></div>
    <div class="mascot-visual" role="img" aria-label="White 3D figure carrying a large green arrow pointing to the call to action"></div>

    <header class="brand">
      <span class="brand-dot"></span>
      <span class="brand-name">Moravintel</span>
    </header>

    <h1 class="headline">
      <span class="headline-year">2018</span>
      <span class="headline-wish">Happy new year</span>
    </h1>

    <a class="cta-button" href="https://www.moravintel.com">Get started now</a>

    <a class="site-address" href="https://www.moravintel.com">www.moravintel.com</a>
  </main>
</body>
</html>
```